2021 Summer Ads Hollis Bay Custom Homes

We need a re-design of our summer ad run for our customer, Hollis Bay Custom Homes. They are custom home builders in the mostly rural parts of West Virginia, USA. They are known for their "Forever Home" tagline. We'd like two designed ads with the main difference being just the custom home that's featured. These designs should be for a Zintrola banner like 300 x 250 and square ad like 250 x 250. For inspiration please visit the Hollis Bay Custom Homes website at www dot hollisbaycustomhomes dot com

Target Market(s)

consumers / new home shoppers

Industry/Entity Type

Consumer

Requirements
Must have
• HBCH logo
Price Lock Available!
Custom home pic
Learn more >
small CFRM logo mark

```html
<!DOCTYPE html>
<html lang="en">
<head>
<meta charset="utf-8">
<title>Hollis Bay Custom Homes – Summer Ads</title>
<link rel="stylesheet" href="https://fonts.googleapis.com/css2?family=Roboto:wght@400;700;900&display=swap">
<style>
  :root {
    --backdrop: #b4b4b4;
    --navy: #1f2633;
    --red: #e31b2b;
    --white: #ffffff;
    --sky: #a9c6e4;
    --foliage: #4f7a3c;
    --stone: #c9c2b4;
  }
  * { box-sizing: border-box; margin: 0; padding: 0; }
  html, body {
    width: 1200px; height: 627px; overflow: hidden;
    background: var(--backdrop);
    font-family: "Roboto", Arial, sans-serif;
  }
  .canvas { position: relative; width: 1200px; height: 627px; }

  .ad {
    position: absolute; top: 101px; height: 426px;
    background: var(--navy); overflow: hidden; color: var(--white);
  }
  .ad--square { left: 90px; width: 426px; }
  .ad--banner { left: 600px; width: 511px; }

  .ad__stripe, .ad__photo { position: absolute; inset: 0; }
  .ad__stripe { background: var(--red); }
  .ad--square .ad__stripe { clip-path: polygon(158px 0, 100% 0, 100% 100%, 266px 100%); }
  .ad--square .ad__photo {
    clip-path: polygon(176px 0, 100% 0, 100% 100%, 288px 100%);
    background: linear-gradient(180deg, var(--sky) 0%, #dfe9f2 22%, var(--foliage) 45%, #6d7f8a 62%, #f1efea 72%, var(--stone) 100%);
  }
  .ad--banner .ad__stripe { clip-path: polygon(260px 0, 100% 0, 100% 100%, 278px 100%); }
  .ad--banner .ad__photo {
    clip-path: polygon(286px 0, 100% 0, 100% 100%, 298px 100%);
    background: linear-gradient(180deg, #6f9fd6 0%, #a8c9ea 25%, #3f6d34 45%, #f3f3f0 60%, #8a8680 78%, #4c6b34 100%);
  }

  .price-tag {
    position: absolute; top: 0; right: 0; width: 153px; height: 34px;
    background: var(--red);
    clip-path: polygon(0 0, 100% 0, 100% 100%, 14px 100%);
    font-size: 12px; font-weight: 700; line-height: 34px;
    text-align: right; padding-right: 10px; color: var(--white);
  }

  .brand {
    position: absolute; top: 40px; display: flex; align-items: center; gap: 8px;
    font-size: 17px; font-weight: 900; letter-spacing: 1px; text-transform: uppercase;
  }
  .brand__mark { width: 12px; height: 12px; background: var(--white); }
  .ad--square .brand { left: 34px; }
  .ad--banner .brand { left: 48px; }

  .headline { position: absolute; font-weight: 700; line-height: 1.18; }
  .ad--square .headline { left: 34px; top: 172px; font-size: 37px; }
  .ad--banner .headline { left: 36px; top: 165px; font-size: 41px; }

  .cta {
    position: absolute; top: 297px; display: flex; align-items: center; gap: 8px;
    color: var(--red); font-size: 19px; font-weight: 700; text-transform: uppercase;
  }
  .ad--square .cta { left: 34px; }
  .ad--banner .cta { left: 36px; }
  .cta__icon { width: 17px; height: 17px; }

  .member-badge {
    position: absolute; top: 380px; width: 40px; height: 32px;
    background: var(--white); border-radius: 3px;
  }
  .ad--square .member-badge { left: 30px; }
  .ad--banner .member-badge { left: 216px; }
</style>
</head>
<body>
<main class="canvas">

  <section class="ad ad--square" aria-label="Square ad">
    <div class="ad__stripe"></div>
    <div class="ad__photo" role="img" aria-label="Photo of a white custom home with a gabled front porch and grey roof, framed by tall green trees under a blue sky"></div>
    <div class="price-tag">price lock available!</div>
    <div class="brand"><span class="brand__mark"></span>Hollis Bay</div>
    <h1 class="headline">Forever<br>Home</h1>
    <div class="cta">Learn More
      <svg class="cta__icon" viewBox="0 0 20 20" aria-hidden="true"><circle cx="10" cy="10" r="10" fill="#e31b2b"/><path d="M8 5.5l4.5 4.5L8 14.5" stroke="#1f2633" stroke-width="2.6" fill="none"/></svg>
    </div>
    <div class="member-badge" role="img" aria-label="CFRM member badge"></div>
  </section>

  <section class="ad ad--banner" aria-label="Banner ad">
    <div class="ad__stripe"></div>
    <div class="ad__photo" role="img" aria-label="Rendering of a white board-and-batten home with stone base, dormers and a dark roof, surrounded by trees and landscaped flower beds"></div>
    <div class="price-tag">price lock available!</div>
    <div class="brand"><span class="brand__mark"></span>Hollis Bay</div>
    <h1 class="headline">Forever<br>Home</h1>
    <div class="cta">Learn More
      <svg class="cta__icon" viewBox="0 0 20 20" aria-hidden="true"><circle cx="10" cy="10" r="10" fill="#e31b2b"/><path d="M8 5.5l4.5 4.5L8 14.5" stroke="#1f2633" stroke-width="2.6" fill="none"/></svg>
    </div>
    <div class="member-badge" role="img" aria-label="CFRM member badge"></div>
  </section>

</main>
</body>
</html>
```